Hedwig Sommerau - Entwicklung für Menschen und Organisationen
Kreative Ideen, die sehr professionell umgesetzt werden und selbstständig verbesserte Versionen werden zur Verfügung gestellt. DANKE!
Zielgruppe
Ich biete Organisationsentwicklungen, Coachings, Teamentwicklungen, Moderationen, Führungskräfteentwicklung, Konfliktklärung und Seminare an.
Meine Zielgruppe sind Vorstände, Geschäftsführer, Personaler, Führungskräfte und andere 'Entscheider'.
Aufgabenstellung
Das Format soll in ein DIN lang Kuvert passen, jedoch gerne nicht das klassische zweifach-gefaltete A4 sein.
Es soll zu meinem Logo und den Druckstücken passen.
Es soll herauskommen, dass alle Leistungen in der Organisationsentwicklung enthalten sein können, diese jedoch auch jeweils einzeln angeboten werden können.
Ich benötige die Broschüre als "offene" Datei, da ich in naher Zukunft die Geschäftsräume wechsele.

```html
<!DOCTYPE html>
<html lang="de">
<head>
<meta charset="utf-8">
<title>Hedwig Sommerau – Mein Angebot</title>
<link rel="stylesheet" href="https://fonts.googleapis.com/css2?family=Open+Sans:wdth,wght@75..100,300..800&display=swap">
<style>
  :root {
    --red: #c80c10;
    --box-light: #7e7364;
    --box-dark: #5a5248;
    --ink: #111111;
    --white: #ffffff;
    --rule: #8a8a8a;
  }
  * { margin: 0; padding: 0; box-sizing: border-box; }
  html, body { width: 1200px; height: 801px; overflow: hidden; background: var(--white); }
  body { font-family: "Open Sans", Arial, sans-serif; color: var(--ink); }
  .brochure { position: relative; width: 1200px; height: 801px; }
  .copy {
    font-size: 13.6px; line-height: 17.6px; font-weight: 400;
    font-stretch: 86%; text-align: justify; hyphens: manual;
  }
  .panel { position: absolute; top: 0; height: 801px; }
  .panel--about { left: 0; width: 403px; }
  .panel--offer { left: 403px; width: 402px; border-left: 1px solid var(--rule); }
  .panel--services { left: 805px; width: 395px; border-left: 1px solid var(--rule); }

  .about-bg { position: absolute; inset: 0; }
  .about-title {
    position: absolute; left: 44px; top: 106px;
    font-size: 28px; font-weight: 600; letter-spacing: 1px; color: var(--white);
  }
  .about-text { position: absolute; left: 44px; top: 190px; width: 318px; color: var(--white); }
  .about-text p + p { margin-top: 17.6px; }

  .offer-title {
    position: absolute; left: 40px; top: 106px;
    font-size: 28px; font-weight: 700; letter-spacing: 1px;
  }
  .offer-intro { position: absolute; left: 43px; top: 189px; width: 319px; }
  .brand {
    position: absolute; left: 40px; top: 326px; width: 320px;
    display: flex; align-items: center; justify-content: center; gap: 10px;
    font-size: 20px; font-weight: 600; color: var(--box-dark);
  }
  .brand-dot { width: 16px; height: 16px; border-radius: 50%; background: var(--red); }

  .info-box {
    position: absolute; border-radius: 3px; color: var(--white);
    padding: 6px 10px 0 10px;
  }
  .info-box h2 { font-size: 14px; font-weight: 700; line-height: 22px; margin-bottom: 2px; }
  .info-box p + p { margin-top: 17.6px; }
  .info-box--main { left: 35px; top: 448px; width: 334px; height: 178px; background: var(--box-light); }

  .offer-closing {
    position: absolute; left: 40px; top: 668px;
    font-size: 27px; font-weight: 700; line-height: 34px; letter-spacing: 0.5px;
  }

  .service {
    position: absolute; left: 14px; width: 372px; border-radius: 3px;
    background: var(--box-dark); color: var(--white);
    padding: 8px 10px 0 52px;
  }
  .service::before {
    content: ""; position: absolute; left: 18px; top: 15px;
    width: 14px; height: 14px; border-radius: 50%; background: rgba(255,255,255,0.85);
  }
  .service h2 { font-size: 14px; font-weight: 700; line-height: 20px; margin-bottom: 4px; }
</style>
</head>
<body>
<main class="brochure">
  <section class="panel panel--about">
    <svg class="about-bg" width="403" height="801" viewBox="0 0 403 801" aria-hidden="true">
      <path d="M0 0 H343 C395 180 410 560 346 801 H0 Z" fill="var(--red)"/>
    </svg>
    <h1 class="about-title">ÜBER MICH</h1>
    <div class="about-text copy">
      <p>Mit meinen über 12 Jahren Erfahrung in der Per&shy;sonal- und Unternehmensentwicklung unterstütze ich Sie gerne bei Ihren Veränderungsprozessen und helfe Ihnen Probleme zu lösen.</p>
      <p>Mit mir profitieren Sie von der Verbindung der bei&shy;den Welten: der Mitarbeiterorientierung sowie die erfolgsorientierten Unternehmensentwicklung.</p>
    </div>
  </section>

  <section class="panel panel--offer">
    <h1 class="offer-title">MEIN ANGEBOT</h1>
    <p class="offer-intro copy">Mein Angebot sind Organisationsentwicklungen als Gesamtprozesse sowie die genannten Leistungen als einzelne Bausteine.</p>
    <div class="brand"><span class="brand-dot"></span>Hedwig Sommerau</div>
    <div class="info-box info-box--main">
      <h2>Organisationsentwicklungen</h2>
      <p class="copy">Größere, geplante und systematische Verände&shy;rungsprozesse mit maximaler Einbindung der Mit&shy;arbeiter innerhalb von Unternehmen oder dessen Teilen, sind Organisationsentwicklungen.</p>
      <p class="copy">Diese sind häufig bei Strategie- und Unterneh&shy;menskulturentwicklungen sowie Änderungen in der Aufbauorganisation anzutreffen.</p>
    </div>
    <h2 class="offer-closing">ZUSÄTZLICH BIETE ICH<br>DIE SECHS LEISTUNGEN<br>AUCH INDIVIDUELL AN.</h2>
  </section>

  <section class="panel panel--services">
    <article class="service" style="top:26px;height:115px">
      <h2>Coaching</h2>
      <p class="copy">Individueller Entwicklungsprozess für eine Person. Ob Mitarbeiter oder Führungskräfte, es gibt ver&shy;schiedenste Themen und Herausforderungen, in denen individuelle Begleitung unterstützen kann.</p>
    </article>
    <article class="service" style="top:148px;height:125px">
      <h2>Führungskräfteentwicklung</h2>
      <p class="copy">Einzelne Qualifizierungen / Coachings oder umfas&shy;sende Führungskräfteprogrammen, die die Ziele und die Strategie des Unternehmens sowie die Individualität der (angehenden) Führungskräfte im Fokus haben.</p>
    </article>
    <article class="service" style="top:281px;height:115px">
      <h2>Konfliktklärungen</h2>
      <p class="copy">Konflikte gehören zum Alltag und sind wichtig für Ent&shy;wicklung. Sie kosten jedoch auch Zeit und viel Geld. Mit Klarheit und Einfühlungsvermögen können im Dialog nachhaltige Lösungen gefunden werden.</p>
    </article>
    <article class="service" style="top:403px;height:115px;padding-top:14px">
      <h2>Moderation</h2>
      <p class="copy">Zielgerichtete und strukturierte Veranstaltungen in einer Atmosphäre, in der sich alle einbringen kön&shy;nen, ermöglichen gute und tragfähige Ergebnisse.</p>
    </article>
    <article class="service" style="top:526px;height:115px">
      <h2>Teamentwicklung</h2>
      <p class="copy">Reflexion, Standortbestimmung, Vertrauen in die Kollegen entwickeln oder Klärung von Konflikten. Dies alles fördert das Potenzial der Mitarbeiter im Team und damit die Motivation und Produktivität.</p>
    </article>
    <article class="service" style="top:648px;height:115px">
      <h2>Seminare</h2>
      <p class="copy">Ein ausgewogenes Verhältnis von Wissensvermitt&shy;lung, ausprobieren und Transfer in den Alltag mit maximalem Praxisbezug, sorgen für nachhaltige Lernerfolge.</p>
    </article>
  </section>
</main>
</body>
</html>
```